Harbor Ledger Funds Bus card and Logo

I need a logo design and Bus card design. The fund focuses on evaluating and investing in minerals (sub-surface rights) and real estate.

Harbor ledger refers to a book of knowledge that each plebe gets when entering the Kelmont Marine Academy (my alma mater)

Target Market(s)

Investors and financial advisors

Contact Information for Business Card

Simple - perhaps a logo with a theme on book of knowledge

Logo Text

Ex Scientia Imperium

Font styles to use
Serif
Sans Serif

Colors

Designer to choose colors to be used in the design.

Requirements
Must have
• memorable logo that is relatively simple

```html
<!DOCTYPE html>
<html lang="en">
<head>
<meta charset="utf-8">
<title>Harbor Ledger Funds – Business Card</title>
<link href="https://fonts.googleapis.com/css2?family=Work+Sans:wght@400;500;600&display=swap" rel="stylesheet">
<style>
  :root {
    --backdrop: #2a2a2a;
    --navy: #143a6a;
    --sky: #1ba8e6;
    --ink: #1e2f4a;
    --paper: #ffffff;
  }
  * { margin: 0; padding: 0; box-sizing: border-box; }
  html, body {
    width: 1200px; height: 900px; overflow: hidden;
    background: var(--backdrop);
    font-family: "Work Sans", Arial, sans-serif;
  }
  .canvas { position: relative; width: 1200px; height: 900px; }
  .card {
    position: absolute; left: 261px; width: 656px; height: 357px;
    overflow: hidden;
    box-shadow: 0 4px 14px rgba(0,0,0,0.45);
  }
  .card--front { top: 69px; background: var(--paper); }
  .card--back { top: 472px; background: var(--navy); }

  .wordmark {
    position: absolute; text-align: center;
    font-weight: 600; letter-spacing: 0.04em; line-height: 1.15;
  }
  .card--front .wordmark {
    left: 32px; width: 280px; top: 150px;
    color: var(--navy); font-size: 26px;
  }
  .card--back .wordmark {
    left: 0; width: 656px; top: 140px;
    color: var(--paper); font-size: 38px;
  }

  .divider {
    position: absolute; left: 338px; top: 90px;
    width: 2px; height: 168px; background: var(--navy);
  }
  .contact { position: absolute; left: 373px; top: 84px; color: var(--ink); }
  .contact__name {
    font-size: 30px; font-weight: 500; color: var(--sky);
    letter-spacing: 0.01em; line-height: 1;
  }
  .contact__role { font-size: 15px; margin-top: 6px; letter-spacing: 0.04em; }
  .contact__address { font-size: 15px; line-height: 21px; margin-top: 14px; letter-spacing: 0.04em; }
  .contact__lines { list-style: none; margin-top: 10px; font-size: 15px; letter-spacing: 0.04em; }
  .contact__lines li { display: flex; align-items: center; height: 21px; }
  .contact__lines svg { width: 10px; height: 10px; margin-right: 8px; flex: none; }

  .wave { position: absolute; left: 0; top: 0; width: 656px; height: 357px; }
</style>
</head>
<body>
<main class="canvas">
  <section class="card card--front">
    <svg class="wave" viewBox="0 0 656 357" preserveAspectRatio="none" aria-hidden="true">
      <path d="M0 284 Q330 380 656 315 L656 357 L0 357 Z" fill="var(--navy)"/>
      <path d="M100 310 Q390 370 656 296 L656 308 Q390 372 100 310 Z" fill="var(--sky)"/>
    </svg>

    <div class="wordmark">HARBOR LEDGER<br>FUNDS LLC</div>
    <div class="divider"></div>

    <div class="contact">
      <div class="contact__name">DANIEL WHITMORE</div>
      <div class="contact__role">Director</div>
      <div class="contact__address">1187 Cedar Hollow Lane<br>Maple Ridge, CA 95310</div>
      <ul class="contact__lines">
        <li>
          <svg viewBox="0 0 10 10"><path d="M2 0.5 L3.6 2.6 L2.7 3.6 Q3.6 5.8 6.2 7.2 L7.2 6.3 L9.4 7.9 L8.4 9.4 Q3.5 9 0.6 1.6 Z" fill="var(--sky)"/></svg>
          +330 5812-4476
        </li>
        <li>
          <svg viewBox="0 0 10 10"><rect x="0.8" y="2" width="8.4" height="6" fill="none" stroke="var(--sky)" stroke-width="1.1"/><path d="M0.8 2 L5 5.4 L9.2 2" fill="none" stroke="var(--sky)" stroke-width="1.1"/></svg>
          info@harborledgerfunds.com
        </li>
        <li>
          <svg viewBox="0 0 10 10"><circle cx="5" cy="5" r="4.2" fill="none" stroke="var(--sky)" stroke-width="1"/><ellipse cx="5" cy="5" rx="1.8" ry="4.2" fill="none" stroke="var(--sky)" stroke-width="0.8"/><path d="M0.8 5 H9.2" stroke="var(--sky)" stroke-width="0.8"/></svg>
          www.harborledgerfunds.com
        </li>
      </ul>
    </div>
  </section>

  <section class="card card--back">
    <div class="wordmark">HARBOR LEDGER<br>FUNDS LLC</div>
  </section>
</main>
</body>
</html>
```